Harborline Lending and Capital. We provide MOSTLY residential home mortgages in Florida AND commercial loans for investment properties throughout the United states.
I would love to emulate so of the lender sites that are available on the internet but I would like to have the site as popular as possible for SEO purposes. Clients can already click the link to take them to the mortgage application where they can complete that and upload documents. If you could polish that up for me that would be great. I can also provide you with great detail on loan programs that are currently being offered. WE OFFER ALL MORTGAGE LENDING PRODUCTS. I would also like to add something in reference to the rate but I don't think it's legal to actually state or promise a rate for mortgage since they vary based on loan type, client and other criteria...

On the Harborline real estate site I would like to add a link or some way for clients to be able to put in credit card information to render services ...

Please let me know what you need from me

Thank you !!

Current link to site to improve and code

https://harborlinelendingandcapital.example/

Industry/Entity Type

Residential and commmercial lending

Coding

Coded - Design and coding required

Number of Pages Required

2 page

Requirements
Must have
• Love to integrate Mortgage interest rates even if general
Nice to have
• Link to fill out mortgage application via Quorvel LPX software

```html
<!DOCTYPE html>
<html lang="en">
<head>
<meta charset="utf-8">
<title>Harborline Lending and Capital</title>
<link rel="stylesheet" href="https://fonts.googleapis.com/css2?family=Fira+Sans:wght@300;400;500;600;700&display=swap">
<style>
:root{
  --green-dark:#1c3a21;
  --green-card:#255c33;
  --green-text:#1f4a27;
  --lime:#9cc33f;
  --cream:#f6f9ec;
  --ink:#222;
  --muted:#444;
  --line:#d9dfc9;
}
*{box-sizing:border-box;margin:0;padding:0}
html,body{width:1200px;height:4441px;overflow:hidden}
body{font-family:"Fira Sans",sans-serif;color:var(--ink);background:#fff;position:relative}
.page-section{position:absolute;left:0;width:1200px}
.abs{position:absolute}
.btn{position:absolute;display:flex;align-items:center;justify-content:center;gap:8px;background:var(--lime);color:var(--green-dark);font-weight:600;font-size:14px;border-radius:2px;text-decoration:none}
.btn .dot{width:14px;height:14px;border-radius:50%;background:var(--green-dark);display:inline-block;position:relative;flex:none}
.btn .dot::after{content:"";position:absolute;left:4px;top:4px;width:5px;height:5px;border-top:1.5px solid var(--lime);border-right:1.5px solid var(--lime);transform:rotate(45deg) translate(-1px,1px)}
.eyebrow{display:flex;align-items:center;gap:8px;color:var(--lime);font-size:12px;letter-spacing:3px;font-weight:600;text-transform:uppercase}
.eyebrow i{width:26px;height:26px;border-radius:50%;background:var(--green-dark);display:inline-block}
.h2{font-size:46px;font-weight:700;color:var(--green-text);line-height:1.1}
.ph{position:absolute}

/* header + hero */
.hero{top:0;height:715px;background:linear-gradient(180deg,#eef2ea 0%,#f3f5ef 60%,#fff 100%)}
.hero .scene{left:0;top:0;width:1200px;height:715px;background:radial-gradient(ellipse at 45% 40%,rgba(205,212,200,.6),rgba(240,243,236,.2) 70%)}
.brand{display:flex;align-items:center;gap:10px;font-weight:700;font-size:15px;color:var(--green-dark)}
.hero .brand{left:86px;top:40px}
.brand i{width:40px;height:40px;background:var(--green-dark);border-radius:50%;flex:none}
.site-nav{right:86px;top:34px;height:44px;display:flex;align-items:center;gap:48px;font-size:14px;font-weight:500;color:#222}
.site-nav .active{color:var(--lime)}
.site-nav .nav-cta{position:static;height:44px;padding:0 20px}
.hero .kicker{left:86px;top:206px;font-size:46px;font-weight:300;color:var(--lime);line-height:56px}
.hero h1{left:86px;top:262px;font-size:48px;line-height:58px;font-weight:700;color:var(--green-text)}
.hero .sub{left:86px;top:399px;font-size:16px;color:#333}
.slider{left:86px;top:617px;display:flex;align-items:center;gap:8px;font-size:22px;color:var(--lime);font-weight:300}
.slider span.bar{width:100px;height:2px;background:#ccc;position:relative}
.slider span.bar::before{content:"";position:absolute;left:0;top:0;width:26px;height:2px;background:var(--lime)}
.slider b{font-size:12px;color:#333;font-weight:500}

/* about */
.about{top:715px;height:635px}
.about .frame{left:107px;top:76px;width:450px;height:418px;border:1.5px solid var(--green-card);border-radius:26px}
.about .photo{left:116px;top:84px;width:451px;height:407px;border-radius:24px;background:linear-gradient(120deg,#3a3532 0%,#8d8c88 45%,#c9d3d9 100%)}
.about .text{left:612px;top:115px;width:450px}
.about h2{margin-top:14px}
.about p{margin-top:22px;font-size:15px;line-height:25px;color:var(--muted)}
.about .cta{margin-top:24px;display:flex;align-items:center;gap:30px}
.about .cta .btn{position:static;width:152px;height:44px}
.call{display:flex;align-items:center;gap:12px}
.call small{display:block;font-size:11px;font-weight:600;letter-spacing:1px}
.call strong{color:var(--lime);font-size:18px;font-weight:600}

/* services */
.services{top:1350px;height:658px;background:var(--cream)}
.services .head{top:50px;width:1200px;text-align:center}
.services .head .eyebrow{justify-content:center}
.services h2{font-size:44px;font-weight:700;color:var(--green-dark);margin-top:4px}
.services h2 span{color:var(--lime)}
.card-img{top:176px;height:240px;width:322px}
.card-body{top:396px;width:288px;height:204px;background:var(--green-card);padding:30px 18px;color:#fff;border-radius:3px}
.card-body h3{font-size:18px;font-weight:600}
.card-body p{margin-top:12px;font-size:15px;line-height:25px;color:#dbe6d8}
.card-body a{display:inline-block;margin-top:12px;color:var(--lime);font-size:14px;font-weight:500;border-bottom:1px solid var(--lime);padding-bottom:2px;text-decoration:none}

/* properties */
.properties{top:2008px;height:661px;background:var(--green-dark)}
.properties .eyebrow{position:absolute;left:86px;top:104px}
.properties h2{position:absolute;left:86px;top:132px;font-size:44px;font-weight:700;color:#fff}
.properties .btn{left:936px;top:130px;width:178px;height:44px}
.prop{top:218px;width:244px;height:344px;border-radius:3px;overflow:hidden}
.prop .label{position:absolute;left:0;bottom:0;height:42px;width:190px;background:var(--lime);color:#fff;font-size:17px;font-weight:500;padding:10px 10px;clip-path:polygon(0 0,82% 0,100% 100%,0 100%)}

/* rates */
.rates{top:2669px;height:653px;background:var(--cream);overflow:hidden}
.rates .circle{left:138px;top:120px;width:420px;height:420px;border-radius:50%;background:var(--lime)}
.rates .person{left:180px;top:38px;width:360px;height:615px;background:linear-gradient(180deg,#3a3a3a 0%,#2a3550 55%,#1f2a44 100%);border-radius:160px 160px 0 0}
.rates .text{left:612px;top:100px;width:520px}
.rates h2{margin-top:6px;font-size:44px}
.rates p{margin-top:10px;font-size:15px;line-height:25px;color:var(--muted)}
.calc{left:612px;top:274px;width:502px;height:252px;background:#e2e6d3;border:1px solid #c9cfb6;border-radius:18px}
.calc .row{position:absolute;left:34px;width:434px;display:flex;justify-content:space-between;font-size:13px;color:#222}
.calc .track{position:absolute;left:34px;width:434px;height:4px;background:#c2c8b0;border-radius:2px}
.calc .track::before{content:"";position:absolute;left:0;top:0;width:214px;height:4px;background:var(--green-card)}
.calc .track::after{content:"";position:absolute;left:206px;top:-6px;width:16px;height:16px;border-radius:50%;background:var(--green-card)}
.calc .btn{left:314px;top:188px;width:152px;height:42px}

/* contact */
.contact-section{top:3322px;height:660px}
.contact-section .head{top:132px;width:1200px;text-align:center}
.contact-section .head .eyebrow{justify-content:center}
.contact-section h2{font-size:44px;color:var(--green-dark);font-weight:700;margin-top:2px}
.contact-section .lead{margin-top:6px;font-size:15px;color:#333}
.field{position:absolute;background:var(--cream);border:1px solid var(--line);font-size:13px;color:#444;padding:12px 14px}
.contact-section .btn{left:531px;top:526px;width:138px;height:43px}

/* footer */
.site-footer{top:3982px;height:459px;background:#13281a;color:#e4eadf}
.site-footer h4{position:absolute;top:108px;color:var(--lime);font-size:14px;letter-spacing:2px;font-weight:600}
.site-footer .brand{left:86px;top:140px;color:#fff;font-size:14px}
.site-footer .brand i{background:#fff}
.site-footer .about-txt{left:86px;top:220px;width:270px;font-size:13.5px;line-height:25px}
.site-footer ul{list-style:none;position:absolute;top:148px;font-size:13.5px;line-height:38px}
.info{left:460px;top:146px;width:210px;font-size:13.5px;line-height:22px}
.info div{display:flex;gap:10px;margin-bottom:16px;word-break:break-all}
.socials{left:1014px;top:150px;display:flex;gap:20px}
.socials span{width:16px;height:16px;border:2px solid #fff;border-radius:3px}
.legal{left:86px;top:411px;width:1028px;display:flex;align-items:center;gap:14px;font-size:13px}
.legal em{font-style:normal;color:var(--lime)}
.legal hr{flex:1;border:0;border-top:1px solid #4b5a4d}
</style>
</head>
<body>

<header class="page-section hero">
  <div class="ph scene" role="img" aria-label="Faded photo of a suburban Florida home"></div>
  <div class="abs brand"><i></i>Harborline Lending and Capital</div>
  <nav class="abs site-nav">
    <span class="active">Home</span><span>About Us</span><span>Our Services</span><span>Properties</span>
    <span class="btn nav-cta">Contact Us <span class="dot"></span></span>
  </nav>
  <div class="abs kicker">Your Best Resource</div>
  <h1 class="abs">For hassle-free, Low cost<br>Mortgage Origination</h1>
  <p class="abs sub">Residential home loans in florida and commercial lending in america</p>
  <a class="btn" style="left:86px;top:448px;width:151px;height:43px">Know More <span class="dot"></span></a>
  <div class="abs slider">01 <span class="bar"></span> <b>04</b></div>
</header>

<section class="page-section about">
  <div class="abs frame"></div>
  <div class="ph photo" role="img" aria-label="Photo of a smiling businesswoman with arms crossed in an office"></div>
  <div class="abs text">
    <div class="eyebrow"><i></i>About</div>
    <h2 class="h2">Harborline Lending<br>and Capital</h2>
    <p>Harborline Lending Originates Residential Home loans in Florida and Commercial and business financing in all 50 States. We have over 25 years of experience in ALL types of real estate and commercial lending.</p>
    <div class="cta">
      <a class="btn">Learn More <span class="dot"></span></a>
      <div class="call">
        <svg width="24" height="24" viewBox="0 0 24 24"><path fill="#1c3a21" d="M6.6 10.8a15 15 0 0 0 6.6 6.6l2.2-2.2a1 1 0 0 1 1-.25 11.4 11.4 0 0 0 3.6.57 1 1 0 0 1 1 1V20a1 1 0 0 1-1 1A17 17 0 0 1 3 4a1 1 0 0 1 1-1h3.5a1 1 0 0 1 1 1c0 1.25.2 2.45.57 3.57a1 1 0 0 1-.25 1z"/></svg>
        <div><small>CALL US</small><strong>1800-555-0199</strong></div>
      </div>
    </div>
  </div>
</section>

<section class="page-section services">
  <div class="abs head">
    <div class="eyebrow"><i></i>Services</div>
    <h2>What We Do <span>For You</span></h2>
  </div>
  <div class="ph card-img" style="left:86px;background:linear-gradient(135deg,#d9d4cc,#6d6660)" role="img" aria-label="Photo of a couple receiving a model house from an agent"></div>
  <div class="ph card-img" style="left:439px;background:linear-gradient(135deg,#e6e6e6,#2f3d5c)" role="img" aria-label="Photo of a businessman at a desk with a piggy bank"></div>
  <div class="ph card-img" style="left:792px;background:linear-gradient(135deg,#e2d8cf,#4a4a48)" role="img" aria-label="Photo of a couple saving coins together"></div>
  <div class="abs card-body" style="left:102px"><h3>Residential Home Mortgages</h3><p>Curabitur quis henulla. Suspendisse sit amet sales arcu. Aenean pharetra varius ultricie</p><a>Learn More ➜</a></div>
  <div class="abs card-body" style="left:455px"><h3>Professional Business Loan</h3><p>Curabitur quis henulla. Suspendisse sit amet sales arcu. Aenean pharetra varius ultricie</p><a>Learn More ➜</a></div>
  <div class="abs card-body" style="left:808px"><h3>Investment Properties Loan</h3><p>Curabitur quis henulla. Suspendisse sit amet sales arcu. Aenean pharetra varius ultricie</p><a>Learn More ➜</a></div>
</section>

<section class="page-section properties">
  <div class="eyebrow"><i style="background:#fff"></i>Properties</div>
  <h2>Available Properties</h2>
  <a class="btn">View All Propertie <span class="dot"></span></a>
  <div class="ph prop" style="left:86px;background:linear-gradient(180deg,#5c8fd6,#e8ebee 60%,#c9c2b6)" role="img" aria-label="Photo of a white apartment tower with balconies"><span class="label">12 Sunset Street</span></div>
  <div class="ph prop" style="left:347px;background:linear-gradient(180deg,#3f7fd0,#e3e4e2 55%,#8a8d86)" role="img" aria-label="Photo of a modern stacked apartment building"><span class="label">34 Union Avenue</span></div>
  <div class="ph prop" style="left:608px;background:linear-gradient(180deg,#b8cfe6,#8c4a34 55%,#6e8a48)" role="img" aria-label="Photo of a brick and white residential block"><span class="label" style="width:210px">56 Washington Street</span></div>
  <div class="ph prop" style="left:869px;background:linear-gradient(180deg,#e5e4df,#9a7b5c 55%,#4d6a3a)" role="img" aria-label="Photo of a townhouse with palm trees"><span class="label">78 Oak Boulevard</span></div>
</section>

<section class="page-section rates">
  <div class="abs circle"></div>
  <div class="ph person" role="img" aria-label="Photo of a man in a suit holding house keys and cash"></div>
  <div class="abs text">
    <div class="eyebrow"><i></i>Interest Rates</div>
    <h2 class="h2">Mortgage Interest Rates</h2>
    <p>Vivamus mattis augue vitae velit congue vestibulum. Curabitur ultricies, metus id lacinia accumsan, nisl dui eleifend augue.</p>
  </div>
  <div class="abs calc">
    <div class="row" style="top:44px"><span>$ 1000</span><span>$ 25,000</span><span>$ 50,000</span></div>
    <div class="track" style="top:84px"></div>
    <div class="row" style="top:126px"><span>1Month</span><span>6 Month</span><span>12Month</span></div>
    <div class="track" style="top:166px"></div>
    <a class="btn">Apply For Loan <span class="dot"></span></a>
  </div>
</section>

<section class="page-section contact-section">
  <div class="abs head">
    <div class="eyebrow"><i></i>Contact Us</div>
    <h2>Get In Touch</h2>
    <p class="lead">Fusce auctor erat erat, eu pulvinar neque iaculis sit amet. Duis ac odio tincidunt</p>
  </div>
  <div class="field" style="left:276px;top:254px;width:317px;height:43px">Name</div>
  <div class="field" style="left:607px;top:254px;width:317px;height:43px">Email</div>
  <div class="field" style="left:276px;top:316px;width:317px;height:43px">Phone</div>
  <div class="field" style="left:607px;top:316px;width:317px;height:43px">Subject</div>
  <div class="field" style="left:276px;top:378px;width:648px;height:124px">How Can We Help You...</div>
  <a class="btn">Submit <span class="dot"></span></a>
</section>

<footer class="page-section site-footer">
  <div class="abs brand"><i></i>Harborline Lending and Capital</div>
  <p class="abs about-txt">Harborline Lending Originates Residential Home loans in Florida and Commercial and business financing in all 50 States. We have over 25 years</p>
  <h4 style="left:460px">CONTACT INFO</h4>
  <div class="abs info">
    <div><span>✉</span><span>info@harborlinelending.example</span></div>
    <div><span>✆</span><span>1800-555-0199</span></div>
  </div>
  <h4 style="left:784px">QUICK LINKS</h4>
  <ul style="left:786px"><li>Home</li><li>About Us</li><li>Our Services</li><li>Properties</li><li>Contact Us</li></ul>
  <h4 style="left:1014px">FOLLOW US</h4>
  <div class="abs socials"><span></span><span></span><span></span></div>
  <div class="abs legal"><span>© 2025 <em>Harborline Lending and Capital Of Florida.</em> All right reserved.</span><hr><span>January 08, 2025.</span></div>
</footer>

</body>
</html>
```